RWT Fittings Ltd Business Cards

We need a business card with our business logo. We provide window and door installations on high-rises in west coast British Colombia, Canada.

I would like my business information and details on one side of the card, and the other side the company name with logo

Target Market(s)

General Contractors

Industry/Entity Type

Construction

Contact Information for Business Card

one side i want my company name and logo in the dark theme logo that i provided

Requirements
Must have
• Marco Peltieri, 16045518293, RWTFittings@mailbox-demo.com, 1407-5194 Linden Row Burnaby BC, V5H 2K9, Owner & Manager

```html
<!DOCTYPE html>
<html lang="en">
<head>
<meta charset="utf-8">
<title>RWT Fittings Ltd – Business Cards</title>
<link rel="stylesheet" href="https://fonts.googleapis.com/css2?family=Open+Sans:wght@400;600;700&display=swap">
<style>
  :root {
    --backdrop-light: #4a4a4a;
    --backdrop-dark: #161616;
    --card: #1b1b1c;
    --brand-blue: #29a9e1;
    --brand-grey: #9a9a9a;
    --ink-light: #f2f2f2;
  }
  * { margin: 0; padding: 0; box-sizing: border-box; }
  html, body { width: 1200px; height: 780px; overflow: hidden; }
  body {
    background: linear-gradient(135deg, var(--backdrop-light), var(--backdrop-dark));
    font-family: "Open Sans", Arial, sans-serif;
    display: flex;
    align-items: center;
    justify-content: center;
    gap: 48px;
  }
  .card {
    position: relative;
    width: 540px;
    height: 309px;
    background: var(--card);
    border-radius: 4px;
    overflow: hidden;
    box-shadow: 0 18px 40px rgba(0,0,0,.55);
  }

  /* Wordmark */
  .wordmark {
    display: flex;
    align-items: center;
    gap: 10px;
    color: var(--brand-blue);
    font-weight: 700;
    letter-spacing: .04em;
    text-transform: uppercase;
    line-height: 1.05;
  }
  .wordmark__square { background: var(--brand-grey); flex: none; }

  /* Front: contact side */
  .card--front .wordmark {
    position: absolute;
    left: 38px;
    top: 50px;
    font-size: 24px;
  }
  .card--front .wordmark__square { width: 30px; height: 30px; }

  .accent-area {
    position: absolute;
    left: 0;
    bottom: 0;
    width: 220px;
    height: 150px;
    background: linear-gradient(160deg, var(--brand-blue) 0%, var(--brand-blue) 60%, var(--brand-grey) 100%);
    border-top-right-radius: 4px;
  }

  .divider {
    position: absolute;
    left: 0; top: 0;
    width: 540px; height: 309px;
  }

  .contact {
    position: absolute;
    left: 300px;
    top: 50px;
    color: var(--ink-light);
    font-size: 12.5px;
    line-height: 1.55;
  }
  .contact__name {
    color: var(--brand-blue);
    font-weight: 700;
    font-size: 19px;
    text-transform: uppercase;
    line-height: 1.15;
  }
  .contact__role { font-size: 14px; margin-bottom: 8px; }
  .contact__line { display: flex; align-items: center; gap: 7px; }
  .contact__line svg { width: 11px; height: 11px; flex: none; fill: var(--brand-blue); }
  .contact__address { margin-top: 8px; }

  /* Back: brand side */
  .card--back { display: flex; align-items: center; justify-content: center; }
  .card--back .wordmark { font-size: 40px; gap: 16px; }
  .card--back .wordmark__square { width: 48px; height: 48px; }
</style>
</head>
<body>

  <section class="card card--front" aria-label="Business card, contact side">
    <div class="accent-area" role="img" aria-label="Decorative blue and grey wave band"></div>

    <div class="wordmark">
      <span class="wordmark__square"></span>
      <span>RWT Fittings<br>Ltd</span>
    </div>

    <svg class="divider" viewBox="0 0 540 309" aria-hidden="true">
      <line x1="285" y1="40" x2="245" y2="215" stroke="var(--brand-blue)" stroke-width="1"/>
    </svg>

    <div class="contact">
      <p class="contact__name">Marco Peltieri</p>
      <p class="contact__role">Owner &amp; Manager</p>
      <p class="contact__line">
        <svg viewBox="0 0 24 24"><path d="M6.6 10.8a15.1 15.1 0 0 0 6.6 6.6l2.2-2.2a1 1 0 0 1 1-.25 11.4 11.4 0 0 0 3.6.57 1 1 0 0 1 1 1V20a1 1 0 0 1-1 1A17 17 0 0 1 3 4a1 1 0 0 1 1-1h3.5a1 1 0 0 1 1 1c0 1.25.2 2.45.57 3.57a1 1 0 0 1-.25 1z"/></svg>
        16045518293
      </p>
      <p class="contact__line">
        <svg viewBox="0 0 24 24"><path d="M2 5h20v14H2z M2 5l10 8 10-8" fill="none" stroke="var(--brand-blue)" stroke-width="2.5"/></svg>
        RWTFittings@mailbox-demo.com
      </p>
      <p class="contact__line">
        <svg viewBox="0 0 24 24"><circle cx="12" cy="12" r="9" fill="none" stroke="var(--brand-blue)" stroke-width="2.5"/><path d="M3 12h18M12 3c3 3 3 15 0 18M12 3c-3 3-3 15 0 18" fill="none" stroke="var(--brand-blue)" stroke-width="1.8"/></svg>
        www.rwtfittings-demo.com
      </p>
      <p class="contact__address">1407-5194 Linden Row<br>Burnaby BC, V5H 2K9</p>
    </div>
  </section>

  <section class="card card--back" aria-label="Business card, brand side">
    <div class="wordmark">
      <span class="wordmark__square"></span>
      <span>RWT Fittings<br>Ltd</span>
    </div>
  </section>

</body>
</html>
```